New Dental Office Needs an Attractive and user friendly Website Designed

I need a website for a new dental office. The Name is Harrowfield Dentistry. I would like a Modern design with a user friendly interface and usability.
I would like a landing page, a page that lists the services we offer: Cosmetic Dentistry, Implants, Dental Hygiene, Emergency Services, Restorations, Dentures
Target Market(s)
Mid to upper class
Industry/Entity Type
Dentistry
Coding
Number of Pages Required
1 page
Requirements
Must have
- Landing page that has a scheduling option, Procedures, operating hours, and contact us info
Nice to have
- Appealing design, Soft comforting colors. Easy to navigate page, Modern and professional.

```html
<!DOCTYPE html>
<html lang="en">
<head>
<meta charset="utf-8">
<title>Harrowfield Dentistry</title>
<link href="https://fonts.googleapis.com/css2?family=Cormorant+Garamond:wght@600;700&family=Roboto:wght@400;500;700&display=swap" rel="stylesheet">
<style>
:root{
  --blue:#1a7ccb;
  --blue-soft:#8fbfe3;
  --ink:#1c1c1c;
  --dark:#1e1e1e;
  --text:#3a3a3a;
  --muted:#555;
  --sky:#e9f6fb;
  --paper:#f3f4f5;
  --foot:#dcedf5;
  --gold:#e0a528;
  --white:#fff;
}
*{box-sizing:border-box;margin:0;padding:0}
html,body{width:1200px;height:4608px;overflow:hidden}
body{position:relative;font-family:'Roboto',Arial,sans-serif;color:var(--text);background:var(--white)}
.abs{position:absolute}
.serif{font-family:'Cormorant Garamond',Georgia,serif;font-weight:700;color:var(--ink)}
.btn{position:absolute;display:flex;align-items:center;justify-content:center;gap:8px;height:40px;border-radius:20px;background:var(--blue);color:var(--white);font-size:12px;font-weight:700}
.btn svg{width:12px;height:12px}
.center{left:0;width:1200px;text-align:center}
.mark{position:absolute;width:30px;height:30px;border-radius:50%;background:var(--blue-soft)}
.label{position:absolute;font-size:20px;font-weight:500;color:var(--blue);letter-spacing:.3px}
.photo{position:absolute}

/* top bar */
.topbar{top:0;left:0;width:1200px;height:40px;background:var(--sky);font-size:13px;font-weight:500;color:var(--ink)}
.topbar .mid{position:absolute;left:445px;width:328px;height:40px;background:var(--ink);color:var(--white);display:flex;align-items:center;justify-content:center;gap:8px}
.topbar .item{position:absolute;top:0;height:40px;display:flex;align-items:center;gap:7px}
.topbar svg{width:12px;height:12px}

/* nav */
.nav{top:40px;left:0;width:1200px;height:98px;background:var(--white)}
.logo{position:absolute;font-family:'Cormorant Garamond',Georgia,serif;font-weight:700;color:var(--ink);text-align:center;line-height:1}
.logo .l1{font-size:38px}
.logo .l2{font-size:17px;letter-spacing:5px;margin-top:2px}
.menu{position:absolute;left:429px;top:45px;display:flex;gap:22px;font-size:13px;font-weight:700;color:var(--ink)}
.menu .on{color:var(--blue)}

/* hero */
.hero{top:138px;left:0;width:1200px;height:520px;overflow:hidden}
.hero h1{position:absolute;left:197px;top:140px;font-size:46px;line-height:47px;color:var(--white)}
.hero p{position:absolute;left:197px;top:306px;font-size:12px;line-height:24px;font-weight:700;color:var(--white);text-transform:uppercase}

/* about */
.about{top:658px;left:0;width:1200px;height:496px;background:linear-gradient(135deg,#f5f5f5,#eceeef 60%,#f4f4f4)}
.h2{position:absolute;font-size:40px}
.para{position:absolute;font-size:14px;line-height:26px;color:var(--text)}

/* services */
.services{top:1154px;left:0;width:1200px;height:1909px;background:var(--sky)}
.rule{position:absolute;height:3px}
.svc-title{position:absolute;display:flex;align-items:center;gap:16px;font-size:31px;font-weight:500;color:var(--ink)}
.svc-title svg{width:34px;height:38px}

/* testimonials */
.testi{top:3063px;left:0;width:1200px;height:472px;background:var(--dark)}

/* contact */
.contact{top:3535px;left:0;width:1200px;height:709px;background:var(--paper)}
.ci{position:absolute;left:111px}
.ci .dot{position:absolute;left:0;width:60px;height:60px;border-radius:50%;background:var(--ink);display:flex;align-items:center;justify-content:center}
.ci .dot svg{width:18px;height:18px}
.ci h4{position:absolute;left:80px;font-size:13px;font-weight:700;color:var(--ink);white-space:nowrap}
.ci span{position:absolute;left:80px;font-size:13px;color:var(--text);white-space:nowrap}
.soc{position:absolute;width:28px;height:28px;border-radius:50%;background:var(--blue-soft)}
.form{position:absolute;left:598px;top:91px;width:490px;height:535px;background:var(--blue)}
.field{position:absolute;left:34px;width:422px;height:47px;background:var(--white);border:1px solid #cfd8df;font-size:13px;color:#666;padding:0 20px;display:flex;align-items:center;justify-content:space-between}
.field svg{width:12px;height:12px}
.submit{position:absolute;left:0;width:490px;top:480px;text-align:center;font-size:14px;font-weight:500;color:var(--white);text-decoration:underline}

/* footer */
.footer{top:4244px;left:0;width:1200px;height:364px;background:var(--foot)}
.fcol{position:absolute;top:73px;font-size:13px;color:var(--ink)}
.fcol h5{font-size:14px;font-weight:700;margin-bottom:17px}
.fcol li{list-style:none;line-height:25px}
.hours td{padding:0 0 0 0;line-height:25px;font-size:13px}
.hours td:first-child{width:63px}
.fsoc{position:absolute;width:26px;height:26px;border-radius:50%;background:var(--white)}
</style>
</head>
<body>

<!-- top bar -->
<header class="abs topbar">
  <div class="item" style="left:111px">
    <svg viewBox="0 0 12 12"><path d="M6 0.5a3.8 3.8 0 0 0-3.8 3.8C2.2 7.2 6 11.5 6 11.5s3.8-4.3 3.8-7.2A3.8 3.8 0 0 0 6 .5zm0 5.3a1.5 1.5 0 1 1 0-3 1.5 1.5 0 0 1 0 3z" fill="#1c1c1c"/></svg>
    48 Alder Lane, USA
  </div>
  <div class="mid">
    <svg viewBox="0 0 12 12"><path d="M3 .8l1.6 2.6-1 1.2a7 7 0 0 0 3.8 3.8l1.2-1 2.6 1.6-.6 2a1 1 0 0 1-1 .6C5 11.3.7 7 .4 2.4a1 1 0 0 1 .6-1z" fill="#fff"/></svg>
    +1 (555) 014 2290
  </div>
  <div class="item" style="left:863px">
    <svg viewBox="0 0 12 12"><rect x=".5" y="2" width="11" height="8" rx="1" fill="#1c1c1c"/><path d="M1 2.8l5 3.6 5-3.6" stroke="#e9f6fb" stroke-width="1" fill="none"/></svg>
    info@harrowfielddentistry.com
  </div>
</header>

<!-- nav -->
<nav class="abs nav">
  <div class="logo" style="left:111px;top:24px;width:208px">
    <div class="l1">Harrowfield</div>
    <div class="l2">DENTISTRY</div>
  </div>
  <div class="menu">
    <span class="on">Home</span><span>About Us</span><span>Our Services</span><span>Testimonials</span><span>Contact Us</span>
  </div>
  <div class="btn" style="left:893px;top:33px;width:195px">
    <svg viewBox="0 0 12 12"><rect x="1" y="2" width="10" height="9" rx="1" fill="#fff"/><rect x="1" y="4" width="10" height=".8" fill="#1a7ccb"/></svg>
    Book Your Appointment
  </div>
</nav>

<!-- hero -->
<section class="abs hero">
  <div class="photo" role="img" aria-label="Smiling young couple posing together, man with arms crossed and woman giving a thumbs up" style="left:0;top:0;width:1200px;height:520px;background:linear-gradient(90deg,#bdbdbd,#a9a9a9 50%,#8f8e8c 75%,#9d9d9b)"></div>
  <svg class="abs" style="left:0;top:0" width="1200" height="520"><polygon points="250,0 676,0 537,520 0,520 0,470" fill="#1c1c1c"/></svg>
  <div class="mark" style="left:328px;top:72px;width:38px;height:38px;background:#fff"></div>
  <h1 class="serif">Smile Brighter<br>with Harrowfield<br>Dentistry</h1>
  <p>From cleanings to cosmetic makeovers. We're<br>here for your healthiest smile.</p>
  <div class="btn" style="left:196px;top:381px;width:196px">
    <svg viewBox="0 0 12 12"><rect x="1" y="2" width="10" height="9" rx="1" fill="#fff"/><rect x="1" y="4" width="10" height=".8" fill="#1a7ccb"/></svg>
    Book Your Appointment
  </div>
</section>

<!-- about -->
<section class="abs about">
  <div class="mark" style="left:585px;top:78px"></div>
  <div class="label center" style="top:122px">ABOUT US</div>
  <h2 class="h2 serif center" style="top:152px">Harrowfield Dentistry</h2>
  <p class="para center" style="top:240px;left:209px;width:784px">Lorem ipsum dolor sit amet, consectetur adipiscing elit, sed do eiusmod tempor incididunt ut labore et dolore magna aliqua. Ut enim ad minim veniam, quis nostrud exercitation ullamco laboris nisi ut aliquip ex ea commodo consequat. Duis aute irure dolor in reprehenderit in voluptate velit esse cillum dolore eu fugiat nulla pariatur. Excepteur sint occaecat cupidatat non proident, sunt in culpa qui officia deserunt mollit anim id est laborum</p>
  <div class="btn" style="left:539px;top:380px;width:122px">Learn More
    <svg viewBox="0 0 12 12"><circle cx="6" cy="6" r="6" fill="#fff"/><path d="M5 3.5L7.5 6 5 8.5" stroke="#1a7ccb" stroke-width="1.6" fill="none"/></svg>
  </div>
</section>

<!-- services -->
<section class="abs services">
  <div class="mark" style="left:585px;top:86px"></div>
  <div class="label center" style="top:130px">OUR SERVICES</div>
  <h2 class="h2 serif center" style="top:164px">What Our Procedures</h2>
  <div class="rule" style="left:557px;top:220px;width:86px;background:var(--ink)"></div>

  <!-- row 1 -->
  <div class="svc-title" style="left:111px;top:338px">
    <svg viewBox="0 0 34 38"><path d="M9 3c-6 0-8 6-6 12 1.5 4 2 8 3 14 .8 5 4 6 5 1l2-8c.8-3 3-3 4 0l2 8c1 5 4.2 4 5-1 1-6 1.5-10 3-14 2-6 0-12-6-12-3 0-5 2-7 2s-4-2-7-2z" fill="none" stroke="#1a7ccb" stroke-width="2.4"/></svg>
    Cosmetic Dentistry
  </div>
  <p class="para" style="left:111px;top:402px;width:430px">Lorem ipsum dolor sit amet, consectetur adipiscing elit, sed do eiusmod tempor incididunt ut labore et dolore magna aliqua. Ut enim ad minim veniam, quis nostrud exercitation ullamco laboris nisi ut aliquip ex ea commodo consequat. Duis aute irure dolor in reprehenderit in voluptate velit esse cillum dolore eu fugiat nulla pariatur. Excepteur sint occaecat cupidatat non proident, sunt in culpa qui officia deserunt mollit anim id est laborum</p>
  <div class="btn" style="left:111px;top:631px;width:124px">Learn More
    <svg viewBox="0 0 12 12"><circle cx="6" cy="6" r="6" fill="#fff"/><path d="M5 3.5L7.5 6 5 8.5" stroke="#1a7ccb" stroke-width="1.6" fill="none"/></svg>
  </div>
  <div class="photo" role="img" aria-label="Smiling woman in a dental chair talking with a dentist" style="left:614px;top:277px;width:474px;height:442px;background:linear-gradient(120deg,#c9b48e,#d8dcd6 45%,#b8bfb8)"></div>

  <!-- row 2 -->
  <div class="photo" role="img" aria-label="Dentist in gloves examining a smiling patient's teeth" style="left:111px;top:792px;width:474px;height:442px;background:linear-gradient(120deg,#6aa6b8,#d9c6b6 45%,#e4e2dd)"></div>
  <div class="svc-title" style="left:669px;top:855px">
    <svg viewBox="0 0 34 38"><path d="M9 3c-6 0-8 6-6 12 1.5 4 2 8 3 14 .8 5 4 6 5 1l2-8c.8-3 3-3 4 0l2 8c1 5 4.2 4 5-1 1-6 1.5-10 3-14 2-6 0-12-6-12-3 0-5 2-7 2s-4-2-7-2z" fill="none" stroke="#1a7ccb" stroke-width="2.4"/><path d="M17 18v16M13 24h8M13 29h8" stroke="#1a7ccb" stroke-width="2"/></svg>
    Dental Implants
  </div>
  <p class="para" style="left:669px;top:918px;width:430px">Lorem ipsum dolor sit amet, consectetur adipiscing elit, sed do eiusmod tempor incididunt ut labore et dolore magna aliqua. Ut enim ad minim veniam, quis nostrud exercitation ullamco laboris nisi ut aliquip ex ea commodo consequat. Duis aute irure dolor in reprehenderit in voluptate velit esse cillum dolore eu fugiat nulla pariatur. Excepteur sint occaecat cupidatat non proident, sunt in culpa qui officia deserunt mollit anim id est laborum</p>
  <div class="btn" style="left:669px;top:1147px;width:124px">Learn More
    <svg viewBox="0 0 12 12"><circle cx="6" cy="6" r="6" fill="#fff"/><path d="M5 3.5L7.5 6 5 8.5" stroke="#1a7ccb" stroke-width="1.6" fill="none"/></svg>
  </div>

  <!-- row 3 -->
  <div class="svc-title" style="left:111px;top:1372px">
    <svg viewBox="0 0 34 38"><path d="M9 3c-6 0-8 6-6 12 1.5 4 2 8 3 14 .8 5 4 6 5 1l2-8c.8-3 3-3 4 0l2 8c1 5 4.2 4 5-1 1-6 1.5-10 3-14 2-6 0-12-6-12-3 0-5 2-7 2s-4-2-7-2z" fill="none" stroke="#1a7ccb" stroke-width="2.4"/><path d="M14 14h6M17 11v6" stroke="#1a7ccb" stroke-width="2"/></svg>
    Emergency Dental Services
  </div>
  <p class="para" style="left:111px;top:1436px;width:430px">Lorem ipsum dolor sit amet, consectetur adipiscing elit, sed do eiusmod tempor incididunt ut labore et dolore magna aliqua. Ut enim ad minim veniam, quis nostrud exercitation ullamco laboris nisi ut aliquip ex ea commodo consequat. Duis aute irure dolor in reprehenderit in voluptate velit esse cillum dolore eu fugiat nulla pariatur. Excepteur sint occaecat cupidatat non proident, sunt in culpa qui officia deserunt mollit anim id est laborum</p>
  <div class="btn" style="left:111px;top:1664px;width:124px">Learn More
    <svg viewBox="0 0 12 12"><circle cx="6" cy="6" r="6" fill="#fff"/><path d="M5 3.5L7.5 6 5 8.5" stroke="#1a7ccb" stroke-width="1.6" fill="none"/></svg>
  </div>
  <div class="photo" role="img" aria-label="Woman on a sofa holding her jaw in tooth pain" style="left:614px;top:1309px;width:474px;height:442px;background:linear-gradient(120deg,#e8e4de,#d8cdbf 45%,#5f7f8c)"></div>

  <div class="btn" style="left:497px;top:1803px;width:206px;background:transparent;border:2px solid var(--ink);color:var(--ink)">View All Services
    <svg viewBox="0 0 12 12"><circle cx="6" cy="6" r="6" fill="#1c1c1c"/><path d="M5 3.5L7.5 6 5 8.5" stroke="#fff" stroke-width="1.6" fill="none"/></svg>
  </div>
</section>

<!-- testimonials -->
<section class="abs testi">
  <div class="mark" style="left:585px;top:80px"></div>
  <div class="label center" style="top:124px">OUR TESTIMONIALS</div>
  <h2 class="h2 serif center" style="top:152px;color:var(--white)">Clients Thinking</h2>
  <div class="rule" style="left:557px;top:214px;width:86px;background:#e9d9b0"></div>
  <div class="abs center" style="top:265px;font-size:17px;font-weight:500;color:var(--white)">MARA QUILL</div>
  <div class="abs center" style="top:292px;font-size:14px;letter-spacing:2px;color:var(--gold)">★★★★★</div>
  <p class="para center" style="left:209px;width:784px;top:324px;color:#e4e4e4">Lorem ipsum dolor sit amet, consectetur adipiscing elit, sed do eiusmod tempor incididunt ut labore et dolore magna aliqua. Ut enim ad minim veniam, quis nostrud exercitation ullamco laboris nisi ut aliquip ex ea commodo consequat. Duis aute irure dolor in reprehenderit in voluptate velit esse cillum</p>
  <svg class="abs" style="left:78px;top:347px" width="12" height="14"><path d="M9 1L3 7l6 6" stroke="#fff" stroke-width="2" fill="none"/></svg>
  <svg class="abs" style="left:1110px;top:347px" width="12" height="14"><path d="M3 1l6 6-6 6" stroke="#fff" stroke-width="2" fill="none"/></svg>
</section>

<!-- contact -->
<section class="abs contact">
  <div class="mark" style="left:113px;top:78px"></div>
  <div class="label" style="left:111px;top:120px">CONTACT US</div>
  <h2 class="h2 serif" style="left:111px;top:150px">Book An Appointment</h2>
  <div class="rule" style="left:111px;top:210px;width:86px;background:var(--ink)"></div>

  <div class="ci" style="top:240px">
    <div class="dot" style="top:0"><svg viewBox="0 0 12 12"><path d="M6 .5a3.8 3.8 0 0 0-3.8 3.8C2.2 7.2 6 11.5 6 11.5s3.8-4.3 3.8-7.2A3.8 3.8 0 0 0 6 .5zm0 5.3a1.5 1.5 0 1 1 0-3 1.5 1.5 0 0 1 0 3z" fill="#fff"/></svg></div>
    <h4 style="top:14px">OUR LOCATION</h4><span style="top:42px">48 Alder Lane, USA</span>
  </div>
  <div class="ci" style="top:328px">
    <div class="dot" style="top:0"><svg viewBox="0 0 12 12"><path d="M3 .8l1.6 2.6-1 1.2a7 7 0 0 0 3.8 3.8l1.2-1 2.6 1.6-.6 2a1 1 0 0 1-1 .6C5 11.3.7 7 .4 2.4a1 1 0 0 1 .6-1z" fill="#fff"/></svg></div>
    <h4 style="top:14px">CALL US</h4><span style="top:42px">+1 555 014 2290</span>
  </div>
  <div class="ci" style="top:417px">
    <div class="dot" style="top:0"><svg viewBox="0 0 12 12"><rect x=".5" y="2" width="11" height="8" rx="1" fill="#fff"/><path d="M1 2.8l5 3.6 5-3.6" stroke="#1c1c1c" stroke-width="1" fill="none"/></svg></div>
    <h4 style="top:14px">EMAIL US</h4><span style="top:42px">info@harrowfielddentistry.com</span>
  </div>
  <div class="soc" style="left:109px;top:510px"></div>
  <div class="soc" style="left:145px;top:510px"></div>
  <div class="soc" style="left:181px;top:510px"></div>
  <div class="soc" style="left:217px;top:510px"></div>
  <div class="btn" style="left:109px;top:563px;width:195px">
    <svg viewBox="0 0 12 12"><rect x="1" y="2" width="10" height="9" rx="1" fill="#fff"/><rect x="1" y="4" width="10" height=".8" fill="#1a7ccb"/></svg>
    Book Your Meeting
  </div>

  <form class="form">
    <div class="field" style="top:50px">First Name <svg viewBox="0 0 12 12"><circle cx="6" cy="3.5" r="2.8" fill="#555"/><path d="M1 12c0-4 2.5-5.5 5-5.5s5 1.5 5 5.5z" fill="#555"/></svg></div>
    <div class="field" style="top:117px">Last Name <svg viewBox="0 0 12 12"><circle cx="6" cy="3.5" r="2.8" fill="#555"/><path d="M1 12c0-4 2.5-5.5 5-5.5s5 1.5 5 5.5z" fill="#555"/></svg></div>
    <div class="field" style="top:183px">Email Address <svg viewBox="0 0 12 12"><rect x=".5" y="2" width="11" height="8" rx="1" fill="#555"/><path d="M1 2.8l5 3.6 5-3.6" stroke="#fff" stroke-width="1" fill="none"/></svg></div>
    <div class="field" style="top:249px">Phone Number <svg viewBox="0 0 12 12"><path d="M3 .8l1.6 2.6-1 1.2a7 7 0 0 0 3.8 3.8l1.2-1 2.6 1.6-.6 2a1 1 0 0 1-1 .6C5 11.3.7 7 .4 2.4a1 1 0 0 1 .6-1z" fill="#555"/></svg></div>
    <div class="field" style="top:315px;height:134px;align-items:flex-start;padding-top:16px">Comments <svg viewBox="0 0 12 12"><ellipse cx="6" cy="5" rx="5" ry="3.5" fill="none" stroke="#555" stroke-width="1.3"/><path d="M3 8l-1 3 3-2" fill="#555"/></svg></div>
    <div class="submit">Submit Here</div>
  </form>
</section>

<!-- footer -->
<footer class="abs footer">
  <div class="logo" style="left:111px;top:70px;width:208px">
    <div class="l1">Harrowfield</div>
    <div class="l2">DENTISTRY</div>
  </div>
  <div class="fcol" style="left:415px">
    <h5>Quick Links</h5>
    <ul><li>Home</li><li>About Us</li><li>Services</li><li>Testimonials</li><li>Contact us</li></ul>
  </div>
  <div class="fcol" style="left:599px">
    <h5>Opening Hours</h5>
    <table class="hours">
      <tr><td>Monday</td><td>9:00 am - 5:00 pm</td></tr>
      <tr><td>Tuesday</td><td>9:00 am - 6:00 pm</td></tr>
      <tr><td>Wednesday</td><td>&nbsp;&nbsp;8:30 am - 6:00 pm</td></tr>
      <tr><td>Thursday</td><td>8:00 am - 7:00 pm</td></tr>
      <tr><td>Friday</td><td>&nbsp;&nbsp;8:30 am - 5:00 pm</td></tr>
      <tr><td>Saturday</td><td>By appointment only</td></tr>
      <tr><td>Sunday</td><td>Closed</td></tr>
    </table>
  </div>
  <div class="fcol" style="left:896px">
    <h5>Contact Us</h5>
    <ul><li>48 Alder Lane, USA</li><li>+1 (555) 014 2290</li><li>info@harrowfielddentistry.com</li></ul>
  </div>
  <div class="fsoc" style="left:899px;top:180px"></div>
  <div class="fsoc" style="left:935px;top:180px"></div>
  <div class="fsoc" style="left:971px;top:180px"></div>
  <div class="fsoc" style="left:1007px;top:180px"></div>
  <div class="abs" style="left:191px;top:288px;width:879px;height:1px;background:#9aa7ae"></div>
  <div class="abs center" style="top:306px;font-size:13px;color:var(--ink)">Copyright@2025.All Rights Reserved</div>
</footer>

</body>
</html>
```